Dog grooming business card
This is a business card for m dog grooming business like it say above.
In the priorities box below I will have the text that I want on the card.

Industry/Entity Type

Business

Colors

Designer to choose colors to be used in the design.

Requirements
Must have
• My logo and the insurance stamp must be on the card.

Text it must have :

Professional grooming services
Email: lunabrisk@mailvale.net
Text or call 1 705 318 6052
TWF certified/member
Pet first aid certified
Next appointment ___________________________________
Nice to have
• Greens to match my logo

```html
<!DOCTYPE html>
<html lang="en">
<head>
<meta charset="utf-8">
<title>Luna Brisk – Grooming Business Card</title>
<link rel="stylesheet" href="https://fonts.googleapis.com/css2?family=Libre+Baskerville:wght@400;700&display=swap">
<style>
  :root {
    --bg: #e9e6e2;
    --card-dark: #2f2a2b;
    --card-light: #ffffff;
    --brand-green: #9cc54a;
    --ink: #1e1b1b;
    --badge-blue: #3f78c4;
    --badge-orange: #ef8a2c;
  }
  html, body {
    margin: 0;
    padding: 0;
    width: 1200px;
    height: 914px;
    overflow: hidden;
    background: var(--bg);
  }
  .canvas {
    position: relative;
    width: 1200px;
    height: 914px;
    display: flex;
    flex-direction: column;
    align-items: center;
    justify-content: center;
    gap: 40px;
  }
  .card {
    position: relative;
    width: 700px;
    height: 400px;
    box-shadow: 0 6px 18px rgba(0,0,0,0.18);
    overflow: hidden;
    font-family: "Libre Baskerville", Georgia, serif;
  }
  .card--front {
    background: var(--card-dark);
    display: flex;
    align-items: center;
    justify-content: center;
  }
  .brand {
    display: flex;
    align-items: center;
    gap: 18px;
    color: var(--brand-green);
    font-weight: 700;
    font-size: 52px;
    letter-spacing: 0.5px;
    white-space: nowrap;
  }
  .brand__dot {
    width: 34px;
    height: 34px;
    border-radius: 50%;
    background: var(--brand-green);
    flex: none;
  }
  .card--back {
    display: flex;
    background: var(--card-light);
  }
  .card__brand-side {
    width: 265px;
    background: var(--card-dark);
    display: flex;
    align-items: center;
    justify-content: center;
  }
  .card__brand-side .brand {
    font-size: 30px;
    gap: 10px;
  }
  .card__brand-side .brand__dot {
    width: 20px;
    height: 20px;
  }
  .card__info {
    position: relative;
    flex: 1;
    padding: 44px 30px 0 34px;
    color: var(--ink);
    font-weight: 700;
    font-size: 20px;
    line-height: 1.62;
  }
  .info__line { margin: 0; }
  .info__line--center { text-align: center; }
  .info__line--indent { padding-left: 22px; }
  .appointment {
    margin-top: 14px;
    font-weight: 400;
    font-size: 17px;
    display: flex;
    align-items: flex-end;
    gap: 18px;
  }
  .appointment__blank {
    flex: 1;
    border-bottom: 1.5px solid var(--ink);
    height: 22px;
  }
  .insurance-badge {
    position: absolute;
    right: 26px;
    bottom: 22px;
    width: 130px;
    height: 64px;
    border: 2px solid var(--badge-blue);
    border-radius: 12px;
    background: #fff;
  }
  .insurance-badge::after {
    content: "";
    position: absolute;
    left: 14px;
    right: 14px;
    top: 27px;
    height: 8px;
    border-radius: 4px;
    background: var(--badge-orange);
  }
</style>
</head>
<body>
  <main class="canvas">
    <section class="card card--front" aria-label="Card front">
      <div class="brand"><span class="brand__dot"></span><span class="brand__name">Luna Brisk</span></div>
    </section>

    <section class="card card--back" aria-label="Card back">
      <div class="card__brand-side">
        <div class="brand"><span class="brand__dot"></span><span class="brand__name">Luna Brisk</span></div>
      </div>
      <div class="card__info">
        <p class="info__line">Professional grooming services</p>
        <p class="info__line info__line--center">1 705 318 6052</p>
        <p class="info__line">lunabrisk@mailvale.net</p>
        <p class="info__line info__line--indent">TWF certified/member</p>
        <p class="info__line info__line--indent">Pet first aid certified</p>
        <div class="appointment"><span>Next appointment</span><span class="appointment__blank"></span></div>
        <div class="insurance-badge" role="img" aria-label="Insurance protection badge"></div>
      </div>
    </section>
  </main>
</body>
</html>
```